Luxury Wine Label for New Startup Winery

We need a wine label for our new winery startup. We have worked with a local designer but do not feel the resulting label / logo have the elevation required to present our brand as a luxury wine. Our winery is called "Quailbrook Vineyards" and we are focused on extremely high quality hand crafted artisan and estate wines from the Pacific Northwest.
We would like to see designs that utilize a tree line, or other imagery that represents the "Quailbrook" part of our company name. Another interesting feature could be wood grain.
A logo will be required based on your design so please design with this in mind:
This logo should be consistent with the wine bottle label design, and should be representative of our high end exclusive wine while giving a sense of place (Oregon/ Pacific Northwest.)
I will supply an image of the design we received from our local designer, PLEASE NOTE: in general we do like wood grain and tree line concepts but feel the execution was poorly done.
ATTN: Logo design should be suitable for use on: Bottles (Red wine/rose/white wine), Bussiness cards, vehicle signage, business signage, etc
P.S.:
If you have a design that is not outside the box we are still interested in seeing it.
Label is for a burgundy style bottle with a label height of 3.5 - 4" and a width of 3.5-4"
any label <= 4"x4" and >=3.5"x3.5" will be acceptable:
HOWEVER Width should be greater than or equal to height due to the bottle format
Target Market(s)
Wine enthusiasts with adequate discretionary budgets to afford $100 bottles of wine.
Industry/Entity Type
Wine / Winery
Requirements
Must have
- A sense of luxury, a feel of exclusivity, and a theme consistent with our product and brand name
Nice to have
- Tree line, wood grain or other wood themes. Serif fonts
Should not have
- anything cheesy, off topic, hard to read script fonts or anything that makes the label hard to read from a few feet away or too busy

```html
<!DOCTYPE html>
<html lang="en">
<head>
<meta charset="utf-8">
<title>Quailbrook Vineyards – Label Collection</title>
<link href="https://fonts.googleapis.com/css2?family=Marcellus&family=Cormorant+Garamond:wght@500&family=Lato:wght@400&display=swap" rel="stylesheet">
<style>
  :root {
    --stage-grey: #7d7d7d;
    --stage-white: #f3f3f3;
    --paper-white: #f0f0f0;
    --paper-shade: #e2e2e2;
    --ink-black: #0d0d0d;
    --ink-shade: #1c1c1c;
    --oak-tan: #c9b396;
    --oak-shade: #bca383;
    --gold-tan: #c4aa85;
    --walnut: #4b3f3a;
    --walnut-shade: #403530;
  }
  * { margin: 0; padding: 0; box-sizing: border-box; }
  html, body { width: 1200px; height: 3333px; overflow: hidden; }
  body { position: relative; background: var(--stage-white); }

  .collection-board {
    position: absolute; left: 0; top: 0;
    width: 1200px; height: 1948px;
    background: var(--stage-grey);
  }
  .bottle-showcase {
    position: absolute; left: 0; top: 1948px;
    width: 1200px; height: 1385px;
    background: var(--stage-white);
  }

  .label {
    position: absolute;
    left: var(--x); top: var(--y);
    width: 53.3em; height: 53.3em;
    font-size: 10px;
    overflow: hidden;
  }
  .label--compact { font-size: 5.5px; }
  .label--medium { font-size: 6px; }

  .label__crest, .label__varietal {
    position: absolute; left: 0; right: 0;
    overflow: hidden;
    color: var(--ink);
    text-align: center;
  }
  .label__crest { top: 0; height: 33.3em; }
  .label__varietal { top: 33.3em; bottom: 0; }

  .wood-grain {
    position: absolute; inset: 0;
    background:
      radial-gradient(ellipse 60% 90% at 70% 80%, var(--shade) 0%, transparent 70%),
      linear-gradient(100deg, var(--panel) 0%, var(--shade) 45%, var(--panel) 100%);
  }

  .emblem-ring {
    position: absolute;
    left: 50%; top: 5.2em;
    width: 15.5em; height: 15.5em;
    margin-left: -7.75em;
    border: 0.28em solid var(--ink);
    border-radius: 50%;
  }
  .wordmark {
    position: absolute; left: 0; right: 0; top: 23em;
    font-family: "Marcellus", serif;
    color: var(--ink);
    line-height: 1;
  }
  .wordmark__name {
    display: block;
    font-size: 4.2em;
    letter-spacing: 0.34em;
    padding-left: 0.34em;
  }
  .wordmark__sub {
    display: block;
    margin-top: 0.3em;
    font-size: 1.6em;
    letter-spacing: 2.05em;
    padding-left: 2.05em;
  }

  .varietal__name, .varietal__vintage, .varietal__region {
    position: absolute; left: 0; right: 0;
    display: block;
    line-height: 1;
    white-space: nowrap;
  }
  .varietal__name {
    top: 1.9em;
    font-family: "Marcellus", serif;
    font-size: 9.4em;
    letter-spacing: 0.04em;
    top: 0.2em;
  }
  .varietal__vintage {
    top: 5.6em;
    font-family: "Cormorant Garamond", serif;
    font-weight: 500;
    font-size: 2.3em;
    letter-spacing: 0.05em;
  }
  .varietal__region {
    top: 7em;
    font-family: "Lato", sans-serif;
    font-size: 2.15em;
    letter-spacing: 0.1em;
  }

  /* colour schemes */
  .on-white  { --panel: var(--paper-white); --shade: var(--paper-shade); --ink: var(--ink-black); }
  .on-black  { --panel: var(--ink-black);   --shade: var(--ink-shade);   --ink: var(--paper-white); }
  .on-black-gold { --panel: var(--ink-black); --shade: var(--ink-shade); --ink: var(--gold-tan); }
  .on-oak    { --panel: var(--oak-tan);     --shade: var(--oak-shade);   --ink: var(--ink-black); }
  .on-walnut { --panel: var(--walnut);      --shade: var(--walnut-shade); --ink: var(--paper-white); }
  .on-white-walnut { --panel: var(--paper-white); --shade: var(--paper-shade); --ink: var(--walnut); }
</style>
</head>
<body>

<section class="collection-board" aria-label="Label colour studies">

  <article class="label" style="--x:47px; --y:65px;">
    <div class="label__crest on-white">
      <div class="wood-grain" role="img" aria-label="White embossed wood grain texture"></div>
      <div class="emblem-ring"></div>
      <div class="wordmark"><span class="wordmark__name">QUAILBROOK</span><span class="wordmark__sub">VINEYARDS</span></div>
    </div>
    <div class="label__varietal on-black">
      <div class="wood-grain" role="img" aria-label="Black wood grain texture"></div>
      <span class="varietal__name">SYRAH</span>
      <span class="varietal__vintage">2024</span>
      <span class="varietal__region">WILLAMETTE VALLEY</span>
    </div>
  </article>

  <article class="label" style="--x:620px; --y:65px;">
    <div class="label__crest on-black">
      <div class="wood-grain" role="img" aria-label="Black wood grain texture"></div>
      <div class="emblem-ring"></div>
      <div class="wordmark"><span class="wordmark__name">QUAILBROOK</span><span class="wordmark__sub">VINEYARDS</span></div>
    </div>
    <div class="label__varietal on-white">
      <div class="wood-grain" role="img" aria-label="White embossed wood grain texture"></div>
      <span class="varietal__name">ROSÉ</span>
      <span class="varietal__vintage">2025</span>
      <span class="varietal__region">WILLAMETTE VALLEY</span>
    </div>
  </article>

  <article class="label" style="--x:47px; --y:699px;">
    <div class="label__crest on-oak">
      <div class="wood-grain" role="img" aria-label="Tan embossed wood grain texture"></div>
      <div class="emblem-ring"></div>
      <div class="wordmark"><span class="wordmark__name">QUAILBROOK</span><span class="wordmark__sub">VINEYARDS</span></div>
    </div>
    <div class="label__varietal on-black-gold">
      <div class="wood-grain" role="img" aria-label="Black wood grain texture"></div>
      <span class="varietal__name">SYRAH</span>
      <span class="varietal__vintage">2024</span>
      <span class="varietal__region">WILLAMETTE VALLEY</span>
    </div>
  </article>

  <article class="label" style="--x:620px; --y:699px;">
    <div class="label__crest on-black-gold">
      <div class="wood-grain" role="img" aria-label="Black wood grain texture"></div>
      <div class="emblem-ring"></div>
      <div class="wordmark"><span class="wordmark__name">QUAILBROOK</span><span class="wordmark__sub">VINEYARDS</span></div>
    </div>
    <div class="label__varietal on-oak">
      <div class="wood-grain" role="img" aria-label="Tan embossed wood grain texture"></div>
      <span class="varietal__name">ROSÉ</span>
      <span class="varietal__vintage">2025</span>
      <span class="varietal__region">WILLAMETTE VALLEY</span>
    </div>
  </article>

  <article class="label" style="--x:47px; --y:1333px;">
    <div class="label__crest on-white">
      <div class="wood-grain" role="img" aria-label="White embossed wood grain texture"></div>
      <div class="emblem-ring"></div>
      <div class="wordmark"><span class="wordmark__name">QUAILBROOK</span><span class="wordmark__sub">VINEYARDS</span></div>
    </div>
    <div class="label__varietal on-walnut">
      <div class="wood-grain" role="img" aria-label="Walnut brown panel"></div>
      <span class="varietal__name">SYRAH</span>
      <span class="varietal__vintage">2024</span>
      <span class="varietal__region">WILLAMETTE VALLEY</span>
    </div>
  </article>

  <article class="label" style="--x:620px; --y:1333px;">
    <div class="label__crest on-walnut">
      <div class="wood-grain" role="img" aria-label="Walnut brown panel"></div>
      <div class="emblem-ring"></div>
      <div class="wordmark"><span class="wordmark__name">QUAILBROOK</span><span class="wordmark__sub">VINEYARDS</span></div>
    </div>
    <div class="label__varietal on-white-walnut">
      <div class="wood-grain" role="img" aria-label="White embossed wood grain texture"></div>
      <span class="varietal__name">ROSÉ</span>
      <span class="varietal__vintage">2025</span>
      <span class="varietal__region">WILLAMETTE VALLEY</span>
    </div>
  </article>
</section>

<section class="bottle-showcase" aria-label="Selected labels">
  <article class="label label--compact" style="--x:211px; --y:887px;">
    <div class="label__crest on-oak">
      <div class="wood-grain" role="img" aria-label="Tan embossed wood grain texture"></div>
      <div class="emblem-ring"></div>
      <div class="wordmark"><span class="wordmark__name">QUAILBROOK</span><span class="wordmark__sub">VINEYARDS</span></div>
    </div>
    <div class="label__varietal on-black-gold">
      <div class="wood-grain" role="img" aria-label="Black wood grain texture"></div>
      <span class="varietal__name">SYRAH</span>
      <span class="varietal__vintage">2024</span>
      <span class="varietal__region">WILLAMETTE VALLEY</span>
    </div>
  </article>

  <article class="label label--medium" style="--x:696px; --y:873px;">
    <div class="label__crest on-black">
      <div class="wood-grain" role="img" aria-label="Black wood grain texture"></div>
      <div class="emblem-ring"></div>
      <div class="wordmark"><span class="wordmark__name">QUAILBROOK</span><span class="wordmark__sub">VINEYARDS</span></div>
    </div>
    <div class="label__varietal on-white">
      <div class="wood-grain" role="img" aria-label="White embossed wood grain texture"></div>
      <span class="varietal__name">ROSÉ</span>
      <span class="varietal__vintage">2025</span>
      <span class="varietal__region">WILLAMETTE VALLEY</span>
    </div>
  </article>
</section>

</body>
</html>
```